Bright and beautiful business card for a coach

I'm a personal and business coach based in Perth, Australia. I need a business card that whilst subtle and elegant, will stand out and appeal on a table full of cards.

My business name is Fern Mentoring and the business card must represent the warmth and brightness implied in the name, without being gimmicky. It must have a warmth and appeal and be easy to read.

I prefer clean, minimalist designs.

It must align with the feel of my website and socials: https://www.fernmentoring-example.com.au/
https://www.instagram.com/fernmentoringau/
https://www.facebook.com/fernmentoringau
Updates

Hi Designers Thank you so much for taking the time to submit designs. I wonder if I could have explained myself a little better. Most of the designs that have been submitted look rather formal and many have quite corporate looking embellishments on them (to my eye). I would like softer, warmer, more organic. I’m open to people playing about and being more abstract, using softer embellishments (e.g the line drawing flowers and grasses I’ve used in my socials) incorporating other colours from my palette or like the social icons in my email signature (in PDF), perhaps playing with size/oversize, playing with the bleed. Please don’t be constrained by what I’ve already done, it merely needs to compliment. I’m sorry if I’m not using the right words or have led you astray. I’m no designer, but I’ve done my website, socials, email signature etc all myself (my logo was a design contest) and I was really hoping for my business card to be something more creative than I could have made with a template. Reminder: No black cards/sides please. Thank you 😊

Target Market(s)

Individuals, most likely but not all female. Creative thinkers. Likely professionals.

Industry/Entity Type

Business & Personal Coach

Contact Information for Business Card

(Fern Mentoring Logo) Name: Greta Pellham; Title: Business & Personal Coach; Phone number: +61 (0)458 913307; Email: greta@fernmentoring-example.com.au; Website: https://fernmentoring-example.com.au; Social icons for Facebook, Instagram & LinkedIn: @fernmentoringAU. Optional strapline: "A thinking partner to help you cut through the noise"

Font styles to use
Sans Serif

Colors
00AB8E
00BBA5
67D7C9
C6EFE9
E9F9F6
59FF00
82FF00
B8FF75
E3FFCB
F4FFEA
FFC000
F8CF3A
FAE287
FDF2CF
FEFAEE

Requirements
Must have
• Must align with feel of my website and socials. Must have a pop of #FFC000 (possibly whole of one side, or at least a block). Bright or white background. Easy to read.
Nice to have
• Possibly incorporate the sunshine/grass picture I have used in website and socials - will upload.
Should not have
• Must not be black or dark. Not impersonal or corporate looking.

```html
<!DOCTYPE html>
<html lang="en">
<head>
<meta charset="utf-8">
<title>Fern Mentoring – Business Card</title>
<link rel="stylesheet" href="https://fonts.googleapis.com/css2?family=Lato:wght@400;700&family=Great+Vibes&display=swap">
<style>
  :root {
    --page: #e9e7e2;
    --sun: #ffc000;
    --white: #ffffff;
    --grass-deep: #2f4a14;
    --grass-mid: #5f8a24;
    --grass-light: #9cc43c;
    --glow: #f3b25a;
    --haze: #d9c7b3;
    --skin-warm: #c48d74;
    --hair: #6b5646;
  }
  * { box-sizing: border-box; margin: 0; padding: 0; }
  html, body { width: 1200px; height: 1015px; overflow: hidden; }
  body {
    background: var(--page);
    font-family: "Lato", sans-serif;
    display: flex;
    flex-direction: column;
    align-items: center;
    justify-content: center;
    gap: 44px;
  }
  .card {
    position: relative;
    width: 720px;
    height: 440px;
    overflow: hidden;
    box-shadow: 0 10px 26px rgba(0,0,0,0.18);
  }
  .meadow-photo {
    position: absolute;
    inset: 0;
    background:
      radial-gradient(ellipse 28% 22% at 56% 6%, rgba(255,236,190,0.95), rgba(243,178,90,0.6) 45%, transparent 100%),
      radial-gradient(ellipse 60% 40% at 60% 0%, var(--haze), transparent 80%),
      linear-gradient(178deg, #8a6a42 0%, var(--grass-light) 38%, var(--grass-mid) 62%, var(--grass-deep) 100%);
  }

  /* Front */
  .brand {
    position: absolute;
    left: 118px;
    top: 150px;
    display: flex;
    align-items: center;
    gap: 14px;
    color: var(--white);
    font-size: 40px;
    font-weight: 400;
    letter-spacing: 1px;
  }
  .brand-dot {
    width: 16px; height: 16px;
    border-radius: 50%;
    background: var(--white);
  }
  .strap-band {
    position: absolute;
    left: 0; right: 0;
    top: 350px;
    height: 34px;
    background: var(--sun);
    display: flex;
    align-items: center;
    padding-left: 74px;
  }
  .strapline {
    color: var(--white);
    font-size: 17px;
    font-weight: 700;
    letter-spacing: 0.3px;
    text-transform: uppercase;
  }

  /* Back */
  .portrait-frame {
    position: absolute;
    inset: 0;
    width: 720px;
    height: 440px;
  }
  .identity {
    position: absolute;
    left: 66px;
    top: 118px;
    color: var(--white);
  }
  .person-name {
    font-family: "Great Vibes", cursive;
    color: var(--sun);
    font-size: 52px;
    font-weight: 400;
    line-height: 1;
  }
  .person-role {
    font-size: 23px;
    margin-top: 6px;
    letter-spacing: 0.3px;
  }
  .contact-list {
    position: absolute;
    left: 66px;
    top: 250px;
    list-style: none;
    color: var(--white);
    font-size: 18px;
    line-height: 28px;
  }
  .contact-list li { display: flex; align-items: center; gap: 12px; }
  .contact-icon { width: 18px; height: 18px; flex: none; }
  .social {
    position: absolute;
    left: 66px;
    top: 352px;
    color: var(--white);
  }
  .social-dots { display: flex; gap: 8px; margin-bottom: 6px; }
  .social-dot {
    width: 28px; height: 28px;
    border-radius: 50%;
    background: var(--sun);
  }
  .social-handle { font-size: 21px; }
</style>
</head>
<body>

  <section class="card card-front">
    <div class="meadow-photo" role="img" aria-label="Sunlit grass meadow photograph with soft line-drawn wildflowers"></div>
    <div class="brand"><span class="brand-dot"></span><span>Fern Mentoring</span></div>
    <div class="strap-band">
      <p class="strapline">A thinking partner to help you cut through the noise</p>
    </div>
  </section>

  <section class="card card-back">
    <div class="meadow-photo" role="img" aria-label="Sunlit grass meadow photograph with soft line-drawn wildflowers"></div>
    <svg class="portrait-frame" viewBox="0 0 720 440" aria-hidden="false">
      <defs>
        <linearGradient id="portraitTone" x1="0" y1="0" x2="1" y2="1">
          <stop offset="0" stop-color="#d8d4cf"/>
          <stop offset="0.45" stop-color="var(--skin-warm)"/>
          <stop offset="1" stop-color="var(--hair)"/>
        </linearGradient>
      </defs>
      <path role="img" aria-label="Portrait photograph of the coach"
            d="M520 0 C440 40 440 150 520 230 C590 300 560 390 520 440 L720 440 L720 0 Z"
            fill="url(#portraitTone)"/>
      <path d="M520 0 C440 40 440 150 520 230 C590 300 560 390 520 440"
            fill="none" stroke="var(--white)" stroke-width="7"/>
    </svg>

    <div class="identity">
      <h1 class="person-name">Greta Pellham</h1>
      <p class="person-role">Business &amp; Personal Coach</p>
    </div>

    <ul class="contact-list">
      <li>
        <svg class="contact-icon" viewBox="0 0 24 24"><path fill="#ffc000" d="M6.6 10.8a15 15 0 0 0 6.6 6.6l2.2-2.2c.3-.3.7-.4 1-.2 1.1.4 2.3.6 3.6.6.6 0 1 .4 1 1V20c0 .6-.4 1-1 1A17 17 0 0 1 3 4c0-.6.4-1 1-1h3.5c.6 0 1 .4 1 1 0 1.3.2 2.5.6 3.6.1.3 0 .7-.2 1z"/></svg>
        +61 (0)458 913307
      </li>
      <li>
        <svg class="contact-icon" viewBox="0 0 24 24"><path fill="#ffc000" d="M2 5h20v14H2z"/><path d="M2 5l10 8 10-8" fill="none" stroke="#2f4a14" stroke-width="1.6"/></svg>
        greta@fernmentoring-example.com.au
      </li>
      <li>
        <svg class="contact-icon" viewBox="0 0 24 24"><circle cx="12" cy="12" r="10" fill="#ffc000"/><path d="M2 12h20M12 2c3 3 3 17 0 20M12 2c-3 3-3 17 0 20M4 7h16M4 17h16" fill="none" stroke="#2f4a14" stroke-width="1.2"/></svg>
        www.fernmentoring-example.com.au
      </li>
    </ul>

    <div class="social">
      <div class="social-dots">
        <span class="social-dot"></span>
        <span class="social-dot"></span>
        <span class="social-dot"></span>
      </div>
      <p class="social-handle">@fernmentoringAU</p>
    </div>
  </section>

</body>
</html>
```